Exclusive beauty salon needs a price list or services booklet

I need a new very attractive flyer for my beauty salon, containing information on the different services and their prices.
In attachment you can find a pdf of the "old" one, but I'd love to have a beautifully designed new one!
I'd love to have a booklet in format 148 x 148 mm, or in US format, containing 12 or 16 pages, but if you can offer other nice looking designs they are welcome!
The services that need to come in the booklet with their prices can all be found on my website: www.atelierverano.be, starting with
Gelaatsverzorging
Wimperverlenging
Suikerontharing
Wimperlifting
Permanente Make Up
Airbrush Tanning

Target Market(s)

woman from 20 to 89 years old

Industry/Entity Type

Beauty Salon

Font styles to use
Sans Serif

Colors

Designer to choose colors to be used in the design.

Requirements
Must have
• a classy nice look, it must contain details about the services from my beauty salon and their prices, and nice pictures.
• The Names, prices and explanations of the services can easily be found on my website: www.atelierverano.be
Nice to have
• In attachment you can find the "old" price list in pdf, what I need now is a "new booklet" with the new logo and updated services price list.
• I need a very nice and attractive looking booklet, classy chique, Paris chique, looking very expensive.
Should not have
• Not too much colors, not too curly, but still feminine

```html
<!DOCTYPE html>
<html lang="nl">
<head>
<meta charset="utf-8">
<title>Atelier Verano – Tarieven &amp; Wimperverlenging</title>
<link rel="stylesheet" href="https://fonts.googleapis.com/css2?family=Lora:wght@400;500&family=Quicksand:wght@400;500&family=Roboto:wght@400;500&display=swap">
<style>
  :root {
    --backdrop: #d6d6d6;
    --paper: #ffffff;
    --paper-left: #f4f4f4;
    --ink: #2a2a2a;
    --ink-soft: #555555;
    --sky: #8fc4d6;
    --sky-light: #cfe6ee;
    --sky-pale: #e6f2f6;
    --rose: #e7a9ae;
    --rose-soft: #f2d3d5;
    --photo-skin: #c9a48e;
    --photo-skin-dark: #9d7a66;
  }
  * { box-sizing: border-box; margin: 0; padding: 0; }
  html, body { width: 1200px; height: 900px; overflow: hidden; }
  body {
    background: var(--backdrop);
    font-family: "Quicksand", sans-serif;
    color: var(--ink);
    position: relative;
  }
  .spread {
    position: absolute;
    left: 80px; top: 186px;
    width: 1040px; height: 528px;
    display: flex;
  }
  .page { position: relative; width: 520px; height: 528px; }
  .page--prices { background: var(--paper-left); }
  .page--lashes { background: var(--paper); }

  /* Prices page */
  .prices-band {
    position: absolute; left: 0; top: 0; width: 100%; height: 56px;
    background: linear-gradient(90deg, var(--sky-light), var(--sky-pale) 45%, var(--sky-light));
  }
  .prices-title {
    position: absolute; left: 0; top: 0; width: 100%; height: 56px;
    display: flex; align-items: center; justify-content: center;
    font-family: "Lora", serif; font-weight: 500;
    font-size: 24px; color: #ffffff; letter-spacing: 0.5px;
  }
  .price-list {
    position: absolute; left: 113px; top: 98px; width: 268px;
    list-style: none;
  }
  .price-row {
    display: flex; justify-content: space-between; align-items: flex-start;
    font-size: 11px; line-height: 14px;
    margin-bottom: 16px;
  }
  .price-row__name { width: 180px; }
  .price-row__amount {
    width: 32px; height: 17px;
    background: var(--sky); color: #fff;
    font-size: 10px; line-height: 17px; text-align: center;
  }

  /* Lashes page */
  .lashes-title {
    position: absolute; top: 32px; left: 0; width: 100%;
    text-align: center;
    font-family: "Lora", serif; font-size: 26px; font-weight: 400;
  }
  .lashes-rule {
    position: absolute; top: 78px; left: 245px; width: 30px; height: 2px;
    background: var(--rose);
  }
  .eye-photo {
    position: absolute; top: 146px; width: 84px; height: 84px;
  }
  .eye-photo--before { left: 44px; background: linear-gradient(160deg, var(--photo-skin), var(--photo-skin-dark)); }
  .eye-photo--after  { left: 143px; background: linear-gradient(160deg, #d4b29e, var(--photo-skin-dark)); }
  .partner-mark {
    position: absolute; top: 262px; left: 44px; width: 183px;
    display: flex; flex-direction: column; align-items: center; gap: 6px;
  }
  .partner-mark__dot { width: 12px; height: 12px; background: var(--ink); }
  .partner-mark__name {
    font-family: "Quicksand", sans-serif; font-weight: 500;
    font-size: 17px; letter-spacing: 3px; color: var(--ink);
  }
  .lashes-caption {
    position: absolute; top: 390px; left: 30px; width: 212px;
    text-align: center; color: var(--rose);
    font-family: "Roboto", sans-serif; font-size: 12.5px; line-height: 16px;
  }
  .lashes-body {
    position: absolute; top: 122px; left: 258px; width: 210px;
    font-size: 11px; line-height: 21.6px; color: var(--ink-soft);
  }
  .page-footer {
    position: absolute; left: 45px; top: 473px; width: 430px;
    display: flex; align-items: center; gap: 10px;
    border-top: 1px solid var(--rose-soft);
  }
  .page-footer__number {
    width: 19px; height: 19px; margin-top: -1px;
    background: var(--rose-soft); color: var(--ink-soft);
    font-size: 12px; text-align: center; line-height: 19px;
  }
  .page-footer__label { color: var(--rose); font-size: 11px; }
  .spine {
    position: absolute; left: 518px; top: 0; width: 4px; height: 528px;
    background: linear-gradient(90deg, rgba(0,0,0,0.06), rgba(0,0,0,0));
  }
</style>
</head>
<body>
  <main class="spread">
    <section class="page page--prices">
      <div class="prices-band" role="img" aria-label="Soft blue floral pattern band"></div>
      <h2 class="prices-title">Tarieven</h2>
      <ul class="price-list">
        <li class="price-row"><span class="price-row__name">wenkbrauwen</span><span class="price-row__amount">€9</span></li>
        <li class="price-row"><span class="price-row__name">wenkbrauwen en bovenlip</span><span class="price-row__amount">€16</span></li>
        <li class="price-row"><span class="price-row__name">bovenlip of kin</span><span class="price-row__amount">€9</span></li>
        <li class="price-row"><span class="price-row__name">bovenlip en kin</span><span class="price-row__amount">€16</span></li>
        <li class="price-row"><span class="price-row__name">gezicht (bovenlip, kin, wangen en wenkbrauw)</span><span class="price-row__amount">€25</span></li>
        <li class="price-row"><span class="price-row__name">Oksels</span><span class="price-row__amount">€12</span></li>
        <li class="price-row"><span class="price-row__name">armen</span><span class="price-row__amount">€20</span></li>
        <li class="price-row"><span class="price-row__name">Brazilian bikini of string</span><span class="price-row__amount">€30</span></li>
        <li class="price-row"><span class="price-row__name">bikinilijn</span><span class="price-row__amount">€15</span></li>
        <li class="price-row"><span class="price-row__name">onderbeen en knie</span><span class="price-row__amount">€30</span></li>
        <li class="price-row"><span class="price-row__name">bovenbenen</span><span class="price-row__amount">€20</span></li>
        <li class="price-row"><span class="price-row__name">volledige benen (zonder bikini)</span><span class="price-row__amount">€50</span></li>
        <li class="price-row"><span class="price-row__name">volledige benen incl. bikinilijn</span><span class="price-row__amount">€59</span></li>
      </ul>
    </section>

    <section class="page page--lashes">
      <h1 class="lashes-title">Wimperverlenging</h1>
      <div class="lashes-rule"></div>
      <div class="eye-photo eye-photo--before" role="img" aria-label="Close-up photo of an eye before lash treatment"></div>
      <div class="eye-photo eye-photo--after" role="img" aria-label="Close-up photo of an eye after lash treatment"></div>
      <div class="partner-mark">
        <span class="partner-mark__dot"></span>
        <span class="partner-mark__name">LUMARA LASHES</span>
      </div>
      <p class="lashes-caption">Lumara<br>Lenght + Volume + Lift voor uw natuurlijke wimpers.</p>
      <p class="lashes-body">
        Het hebben van mooie, lange en volumineuze wimpers staat hoog op het verlanglijstje van vele vrouwen. Het liefst heeft men de wimpers mooi gelift voor een open blik die de ogen optisch groter maakt. Niet voor niets is mascara één van de best verkochte make-upproducten.<br>
        De nieuwe en revolutionaire Lumara-methode zorgt echter na slechts 1 behandeling van 60 minuten, gedurende minimaal 6 weken voor Lange, Volumineuze en geLifte wimpers. Dit alles, zonder dat daar een wimperkrultang of dikke lagen mascara aan te pas hoeven te komen!
      </p>
      <footer class="page-footer">
        <span class="page-footer__number">4</span>
        <span class="page-footer__label">Wimperverlenging</span>
      </footer>
    </section>
    <div class="spine"></div>
  </main>
</body>
</html>
```